Cloud Hosted Phone System for small and medium sized businesses

I want to design a one A4 page size single or double sided brochure to offer cloud hosted VoIP Phone system and a complete collaboration system. We have partnered with a VoIP Phone system company and want to sell their services but we don't want their name to be shown on the brochure because customers might call them directly. The company name is Vornel (www.vornel-example.com) and our company name is KESTRAL Tech Solutions. I have also uploaded my compnay's logo that you should show on the brochure. For more details about the product, you can visit their website as mentioned above.

Reason: Not getting a design to my liking.

Target Market(s)

Small and medium sized business including law firms, marketing and advertising agencies, real-estate firms and others.

Industry/Entity Type

Voip

Colors

Designer to choose colors to be used in the design.

Requirements
Must have
• My company's Logo (KESTRAL Tech Solutions). Price list, services and some images to show the benefits and services of the cloud based and advanced VoIP phone system. I want the brochure to look very professional and attractive.
• Contact US: Our company's name, Logo, web address, phone (555-730-4186) and email (info@kestraltechsolutions-example.com)
Nice to have
• It is a Canadian based company and all of our servers and customers’ data reside in Canada.

```html
<!DOCTYPE html>
<html lang="en">
<head>
<meta charset="utf-8">
<title>KESTRAL Tech Solutions – Cloud-Based Phone System</title>
<link rel="stylesheet" href="https://fonts.googleapis.com/css2?family=Fira+Sans:wght@600;700;800&family=Open+Sans:wght@400;600;700&display=swap">
<style>
  :root {
    --brand-blue: #0b5aa6;
    --deep-blue: #0a4c95;
    --ink: #1f2227;
    --body: #2b2e33;
    --black: #0b0b0c;
    --white: #ffffff;
    --photo-dark: #1c2733;
    --photo-cable: #3f8fd6;
  }
  * { margin: 0; padding: 0; box-sizing: border-box; }
  html, body { width: 932px; height: 1200px; overflow: hidden; background: var(--white); }
  .flyer {
    position: relative; width: 932px; height: 1200px; overflow: hidden;
    background: var(--white); font-family: "Open Sans", Arial, sans-serif; color: var(--body);
  }
  .header-art { position: absolute; left: 0; top: 0; width: 932px; height: 430px; }

  .brand {
    position: absolute; top: 398px; left: 0; width: 932px;
    display: flex; justify-content: center; align-items: center; gap: 14px;
  }
  .brand-dot { width: 58px; height: 58px; border-radius: 50%; background: var(--brand-blue); }
  .brand-name {
    font-family: "Open Sans", Arial, sans-serif; font-weight: 600; color: var(--ink);
    font-size: 40px; line-height: 1;
  }
  .brand-name small { display: block; font-size: 22px; margin-top: 4px; }

  .intro { position: absolute; left: 58px; top: 480px; width: 820px; }
  .title {
    font-family: "Fira Sans", Arial, sans-serif; font-weight: 700; font-size: 27px;
    color: var(--brand-blue); letter-spacing: 0.2px; line-height: 1.1;
  }
  .intro p { font-size: 14px; line-height: 19.5px; margin-top: 8px; }
  .intro p + p { margin-top: 10px; }

  .benefits { position: absolute; left: 58px; top: 656px; width: 820px; }
  .benefits h2 {
    font-family: "Fira Sans", Arial, sans-serif; font-weight: 800; font-size: 25px;
    color: var(--ink); line-height: 1.1;
  }
  .benefit { margin-top: 12px; }
  .benefit h3 {
    position: relative; padding-left: 33px;
    font-family: "Fira Sans", Arial, sans-serif; font-weight: 600; font-size: 21px;
    color: var(--brand-blue); line-height: 1.1;
  }
  .benefit h3::before {
    content: ""; position: absolute; left: 2px; top: 6px; width: 9px; height: 9px;
    border: 2px solid var(--brand-blue); border-radius: 50%;
  }
  .benefit p { padding-left: 33px; font-size: 14px; line-height: 19.5px; margin-top: 4px; }

  .services {
    position: absolute; left: 0; top: 1022px; width: 932px; height: 139px;
    background: linear-gradient(180deg, #1769c2 0%, var(--deep-blue) 100%);
    color: var(--white); text-align: center;
  }
  .services-title {
    font-family: "Fira Sans", Arial, sans-serif; font-weight: 600; font-size: 25px;
    padding-top: 8px; line-height: 1.2;
  }
  .services-rule { width: 560px; height: 1px; margin: 4px auto 0; background: rgba(255,255,255,0.8); position: relative; }
  .services-rule::after { content: ""; position: absolute; left: 180px; top: -1px; width: 200px; height: 3px; background: var(--white); }
  .services-list { display: flex; justify-content: center; margin-top: 8px; }
  .service {
    width: 200px; height: 88px; display: flex; flex-direction: column; align-items: center; justify-content: space-between;
    font-size: 14.5px; padding-bottom: 2px;
  }
  .service + .service { border-left: 1px solid rgba(255,255,255,0.8); }
  .service svg { width: 56px; height: 56px; }

  .contact-bar {
    position: absolute; left: 0; top: 1161px; width: 932px; height: 39px; background: var(--black);
    color: var(--white); display: flex; align-items: center; justify-content: center;
    font-size: 14.5px; gap: 14px;
  }
  .contact-bar b { font-weight: 700; }
  .contact-sep { width: 1px; height: 22px; background: rgba(255,255,255,0.8); }
  .contact-item { display: flex; align-items: center; gap: 8px; }
  .contact-item svg { width: 16px; height: 16px; }
</style>
</head>
<body>
<main class="flyer">
  <svg class="header-art" viewBox="0 0 932 430" aria-hidden="false">
    <defs>
      <linearGradient id="photoTone" x1="0" y1="0" x2="1" y2="1">
        <stop offset="0" stop-color="#c9d4de"/>
        <stop offset="0.35" stop-color="var(--photo-cable)"/>
        <stop offset="0.7" stop-color="#34414f"/>
        <stop offset="1" stop-color="var(--photo-dark)"/>
      </linearGradient>
    </defs>
    <path role="img" aria-label="Photo of blue network cables plugged into a server switch"
          d="M0 0 H932 V124 Q466 522 0 124 Z" fill="url(#photoTone)"/>
    <path d="M0 124 Q466 522 932 124 V233 Q466 523 0 233 Z" fill="var(--black)"/>
    <path d="M0 250 Q120 340 250 372 V418 Q110 385 0 320 Z" fill="var(--brand-blue)"/>
    <path d="M932 250 Q812 340 682 372 V418 Q822 385 932 320 Z" fill="var(--brand-blue)"/>
  </svg>

  <div class="brand">
    <span class="brand-dot"></span>
    <div class="brand-name">KESTRAL<small>Tech Solutions</small></div>
  </div>

  <section class="intro">
    <h1 class="title">A CLOUD-BASED PHONE SYSTEM FOR BUSINESSES</h1>
    <p>We can help you grow your business by modernizing your company's phone system and making it easy to use, manage, and track directly from the cloud</p>
    <p>Our cloud business phone system adapts to your economic challenges and brings flexibility and adaptability to your business communications whilst considerably reducing costs compared to traditional phone systems. We take great pride in continually improving our platform as well as developing new features and services that in turn increase our customers' productivity.</p>
  </section>

  <section class="benefits">
    <h2>BENEFITS OF CLOUD-BASED PHONE SYSTEM</h2>
    <div class="benefit">
      <h3>Become Mobile</h3>
      <p>From our cloud-based telephony and its unified communications system emerges the concept of mobility. Make calls using your office phone, computer, or mobile phone, and chat with your colleagues and customers from numerous locations. Enjoy centralized communications and simplified management.</p>
    </div>
    <div class="benefit">
      <h3>Stay Abreast</h3>
      <p>Enjoy leading-edge telecommunications technology and its host of features that adapt to your needs, whatever the size of your business. These features are constantly upscaled and automatically updated. You will thus never have to operate an obsolete system.</p>
    </div>
    <div class="benefit">
      <h3>Avoid Inconveniences</h3>
      <p>We take charge of the structure of your business phone system and remove the PBX (Private Branch Exchange) system to host it in its cloud database, thus saving you space, time, and costs. You are cleared of wire clutter and your business communications are streamlined, allowing you to work freely and efficiently. Also, this service includes an excellent recovery and business continuity plan that prevents unforeseen events, such as claims or system failures, from leading to data loss or suspension of business activities.</p>
    </div>
  </section>

  <section class="services">
    <h2 class="services-title">A Cloud-based Phone System For Businesses</h2>
    <div class="services-rule"></div>
    <div class="services-list">
      <div class="service">
        <svg viewBox="0 0 56 56" fill="#fff"><rect x="8" y="14" width="10" height="36" rx="3"/><rect x="20" y="18" width="26" height="32" rx="3"/><rect x="24" y="22" width="18" height="7" fill="#1769c2"/><g fill="#1769c2"><rect x="24" y="32" width="4" height="4"/><rect x="31" y="32" width="4" height="4"/><rect x="38" y="32" width="4" height="4"/><rect x="24" y="39" width="4" height="4"/><rect x="31" y="39" width="4" height="4"/><rect x="38" y="39" width="4" height="4"/></g><path d="M34 12a6 6 0 0 1 11-3 5 5 0 0 1 5 5h-16z" fill="none" stroke="#fff" stroke-width="2"/></svg>
        <span>Cloud Phone System</span>
      </div>
      <div class="service">
        <svg viewBox="0 0 56 56" fill="#fff"><circle cx="14" cy="12" r="5"/><circle cx="28" cy="9" r="5"/><circle cx="42" cy="12" r="5"/><rect x="8" y="19" width="12" height="16" rx="3"/><rect x="22" y="16" width="12" height="16" rx="3"/><rect x="36" y="19" width="12" height="16" rx="3"/><rect x="12" y="36" width="32" height="4"/><rect x="15" y="40" width="4" height="12"/><rect x="37" y="40" width="4" height="12"/></svg>
        <span>Unified Communications</span>
      </div>
      <div class="service">
        <svg viewBox="0 0 56 56" fill="none" stroke="#fff" stroke-width="4"><path d="M12 30v-4a16 16 0 0 1 32 0v4"/><rect x="8" y="28" width="8" height="14" rx="3" fill="#fff"/><rect x="40" y="28" width="8" height="14" rx="3" fill="#fff"/><path d="M44 42q0 8-12 8h-4" stroke-width="3"/></svg>
        <span>Contact Center</span>
      </div>
      <div class="service">
        <svg viewBox="0 0 56 56" fill="#fff"><circle cx="18" cy="10" r="6"/><rect x="12" y="18" width="12" height="18" rx="3"/><rect x="12" y="34" width="20" height="5"/><rect x="27" y="34" width="5" height="16"/><rect x="8" y="22" width="4" height="28"/><rect x="28" y="26" width="24" height="4"/><rect x="46" y="30" width="4" height="20"/><path d="M38 26l6-12h3l-6 12z"/></svg>
        <span>Meet Studio</span>
      </div>
    </div>
  </section>

  <footer class="contact-bar">
    <span>Call Us: <b>555-730-4186</b></span>
    <span class="contact-sep"></span>
    <span class="contact-item">
      <svg viewBox="0 0 16 16" fill="none" stroke="#fff" stroke-width="1.3"><circle cx="8" cy="8" r="7"/><ellipse cx="8" cy="8" rx="3" ry="7"/><path d="M1 8h14"/></svg>
      <span>www.<b>kestraltechsolutions-example</b>.com</span>
    </span>
    <span class="contact-sep"></span>
    <span class="contact-item">
      <svg viewBox="0 0 16 16" fill="none" stroke="#fff" stroke-width="1.3"><circle cx="8" cy="8" r="7"/><path d="M5.5 4.5l1.5 2-1 1a5 5 0 0 0 2.5 2.5l1-1 2 1.5-1 1.5c-3 0-6-3-6-6z" fill="#fff" stroke="none"/></svg>
      <span>info@<b>kestraltechsolutions-example</b>.com</span>
    </span>
  </footer>
</main>
</body>
</html>
```